Cat-products company needs smart, yet endearing, business card

We need a business card design for a new, but up-and-running, business based in Honolulu, Hawaii. The business is Purrnest Nook Co. Our first product is the most environmentally-friendly cat grass kit ever seen on the planet. Future products, currently in the R&D phase, will include a variety of exciting cat scratchers. We also do consulting work to help apartment-dwellers make their home more cat-friendly and, in the future, plan on doing full, custom installs of structure to create high walkways for cats.

Target Market(s)

Middle-aged, apartment-dwelling, middle-class workers who own 1 or more cats and who dote on them.

Industry/Entity Type

Pet Care

Contact Information for Business Card

A striking, professional, yet warm and friendly design is what we're after.

Font styles to use
Serif
Sans Serif
Other font styles liked:
• Comfortaa

Colors

Designer to choose colors to be used in the design.

Requirements
Must have
• The company logo: (see attachment)
• The company name: Purrnest Nook Co
• The web address: www.purrnestnookco.com
• Email: support@purrnestnookco.com
• Phone: +1 (808) 571 6023
• Update (Fri Jun 30 3017 7:45pm Hawaii Time) I would like, is possible, uploaded picture of the cat grass kit on the back of the card with some text along the lines of: Purrnest Nook Co - Maker Of The Leafiest Feline Sprout Set Yet
Nice to have
• A cat picture, cartoon, real or silhouette that illustrates cats in action and/or relaxing; ie using the apartment space to live, play and relax in and being well-contented.
• Most of the website is done in the font: Comfortaa. It might be nice to continue using this for brand consistency.
Should not have
• Hard-to-read fonts.

```html
<!DOCTYPE html>
<html lang="en">
<head>
<meta charset="utf-8">
<title>Purrnest Nook Co — Business Card</title>
<link rel="stylesheet" href="https://fonts.googleapis.com/css2?family=Comfortaa:wght@400;600;700&display=swap">
<style>
  :root {
    --brown: #4b2a1f;
    --yellow: #f4b01b;
    --ink: #2b2b2b;
    --muted: #6b6b6b;
    --paper: #ffffff;
    --backdrop: #e4e4e2;
    --font: "Comfortaa", sans-serif;
  }
  * { box-sizing: border-box; margin: 0; padding: 0; }
  html, body { width: 1200px; height: 1000px; overflow: hidden; }
  body {
    background: var(--backdrop);
    font-family: var(--font);
    position: relative;
  }
  .card {
    position: absolute;
    left: 250px;
    width: 700px;
    height: 400px;
    background: var(--paper);
    box-shadow: 0 6px 18px rgba(0,0,0,0.18);
    overflow: hidden;
  }
  .card--front { top: 60px; }
  .card--back { top: 540px; }

  .brand {
    display: flex;
    align-items: center;
    gap: 12px;
    color: var(--brown);
    font-weight: 700;
    letter-spacing: 0.01em;
  }
  .brand__dot {
    width: 22px; height: 22px;
    border-radius: 50%;
    background: var(--yellow);
    flex: none;
  }
  .card--front .brand {
    position: absolute;
    left: 50%; top: 50%;
    transform: translate(-50%, -50%);
    font-size: 34px;
    white-space: nowrap;
  }
  .card--back .brand {
    position: absolute;
    left: 44px; top: 70px;
    font-size: 26px;
    white-space: nowrap;
  }

  .person {
    position: absolute;
    right: 44px; top: 128px;
    text-align: right;
  }
  .person__name {
    color: var(--yellow);
    font-weight: 700;
    font-size: 30px;
    letter-spacing: 0.02em;
  }
  .person__title {
    color: var(--muted);
    font-size: 17px;
    margin-top: 4px;
  }

  .rule { position: absolute; top: 232px; height: 3px; }
  .rule--yellow { left: 0; width: 430px; background: var(--yellow); }
  .rule--brown { left: 440px; right: 0; background: var(--brown); }

  .contacts {
    position: absolute;
    right: 44px; top: 254px;
    list-style: none;
    text-align: right;
    font-size: 16px;
    color: var(--ink);
    line-height: 26px;
  }
  .contacts li { display: flex; justify-content: flex-end; align-items: center; gap: 12px; }
  .contacts .icon { width: 15px; height: 15px; flex: none; }
  .contacts .accent { color: var(--yellow); }

  .address {
    position: absolute;
    left: 92px; top: 318px;
    font-size: 17px;
    line-height: 24px;
    color: var(--ink);
  }
</style>
</head>
<body>
  <section class="card card--front" aria-label="Card front">
    <div class="brand"><span class="brand__dot"></span>Purrnest Nook Co</div>
  </section>

  <section class="card card--back" aria-label="Card back">
    <div class="brand"><span class="brand__dot"></span>Purrnest Nook Co</div>

    <div class="person">
      <div class="person__name">Lena Kahale</div>
      <div class="person__title">Director</div>
    </div>

    <div class="rule rule--yellow"></div>
    <div class="rule rule--brown"></div>

    <ul class="contacts">
      <li>+1 (808) 571 6023
        <svg class="icon" viewBox="0 0 16 16" aria-hidden="true"><path fill="var(--yellow)" d="M3.6 1.5l2.3 2.6-1.3 1.8c.9 2 2.5 3.6 4.5 4.5l1.8-1.3 2.6 2.3-1.4 2.1C7 13.3 2.7 9 1.5 3z"/></svg>
      </li>
      <li>support@purrnestnookco.com
        <svg class="icon" viewBox="0 0 16 16" aria-hidden="true"><rect x="1" y="3" width="14" height="10" rx="1" fill="var(--yellow)"/><path d="M1.5 3.8L8 9l6.5-5.2" stroke="#fff" stroke-width="1.3" fill="none"/></svg>
      </li>
      <li><span>www.<span class="accent">purrnestnookco</span>.com</span>
        <svg class="icon" viewBox="0 0 16 16" aria-hidden="true"><g fill="none" stroke="var(--yellow)" stroke-width="1.3"><circle cx="8" cy="8" r="6.5"/><ellipse cx="8" cy="8" rx="2.8" ry="6.5"/><path d="M1.5 8h13M2.5 4.8h11M2.5 11.2h11"/></g></svg>
      </li>
    </ul>

    <address class="address" style="font-style:normal">Your Street Address,<br>Country,1234</address>
  </section>
</body>
</html>
```